A4 Single Page Brochure for Private Cloud Offerings

Theme: Futuristic Tech Company

Meridane Systems is looking to offer private cloud services for our enterprise customers in Perth-based data-centres that provides our clients with a lower-cost alternative to Kelvara or QNL yielding better performance.

We are looking for a single A4 brochure with a great graphics design theme to promote these services.

We will be providing five tiers:
- Starter
- Growth
- Professional
- Premier
- Elite

Each plan must list on the brochure the Max VMs, CPU cores, Memory and SSD storage allocated. Refer to the uploaded PNG file.

The brochure must list the following selling points:

- Hosted in a local Perth-based TIER3 and TIER4 datacentres
- WA owned hosting - support local
- Low latency - ultra fast local hosting
- Includes Orvix Host Datacentre licensing
- Includes BrakWall Managed Firewalls for Enterprise level threat detection
- Includes all infrastructure maintenance services
- Full self management of VMs through customer portal
- Includes a 1gbps Internet link
- Predictable fixed monthly fee with no dynamic billing
- No additional charges for Storage Transactions, Internet Usage, VM Snapshots, Datacentre Bandwidth Usage and Firewall Traffic Usage.
- Highly available cluster, no single point of failure.
- Pricing is based on 36 months commit
- Yearly rate increases capped to a maximum of Australian CPI
- All plans have 24/7/365 support with dedicated after hours number.
- Managed backup and managed disaster recovery services can be added to plans

Service provided in accordance with our terms and conditions.

We need the ability to EDIT the brochure to adjust pricing after we receive the final project.

I have uploaded more details on these plans under the attachment PrivateCloudPlans.png.

Please do not utilise "Pushing the Boundaries of Technology" - our brand is being replaced with "Specialised Consulting". New website is under development but not launched yet.

Target Market(s)

Information Technology Sector

Colors
0054AA
0677BA
7BADD7
CADEEF
E8F1F8

Requirements
Must have
• Theme of Meridane is Blue
Should not have
• Extremely stock imagary that just looks "cheap and stock"

```html
<!DOCTYPE html>
<html lang="en">
<head>
<meta charset="utf-8">
<title>Meridane Systems – Private Cloud Plans</title>
<link rel="stylesheet" href="https://fonts.googleapis.com/css2?family=Bebas+Neue&family=Oswald:wght@400;500&family=Roboto:wght@400;500&display=swap">
<style>
  :root{
    --navy:#1d1b72;
    --blue:#1f4fae;
    --blue-deep:#163a86;
    --sky:#7badd7;
    --pale:#e8f1f8;
    --grey:#7c7c80;
    --grey-dark:#5d5d62;
    --grey-light:#eef0f3;
    --white:#ffffff;
    --text:#4a4a52;
  }
  *{box-sizing:border-box;margin:0;padding:0}
  html,body{width:1050px;height:1200px;overflow:hidden;background:var(--white)}
  .brochure{position:relative;width:1050px;height:1200px;overflow:hidden;
    background:linear-gradient(180deg,#f4f5f7 0%,var(--grey-light) 45%,#f7f8fa 60%,var(--white) 100%);
    font-family:"Roboto",Arial,sans-serif;color:var(--text)}
  .brand{position:absolute;left:82px;top:70px;display:flex;align-items:center;gap:14px}
  .brand-mark{width:30px;height:30px;background:var(--navy)}
  .brand-name{font-family:"Roboto",Arial,sans-serif;font-weight:500;font-size:28px;color:var(--navy);letter-spacing:1px;line-height:1}
  .headline{position:absolute;left:80px;top:200px;font-family:"Bebas Neue",Impact,sans-serif;font-weight:400;line-height:.92}
  .headline span{display:block}
  .headline .line-navy{color:var(--navy);font-size:96px}
  .headline .line-grey{color:var(--grey);font-size:128px}
  .hero-visual{position:absolute;left:412px;top:16px;width:638px;height:502px;
    background:linear-gradient(160deg,var(--navy) 0%,#0677ba 45%,var(--sky) 70%,#c9ccd3 100%)}
  .cloud-strip{position:absolute;left:0;top:512px;width:380px;height:58px;
    background:linear-gradient(180deg,var(--blue) 0%,var(--sky) 45%,var(--white) 100%)}
  .intro{position:absolute;left:82px;top:610px;width:440px;font-size:17px;line-height:1.3;color:var(--text)}
  .plans-band{position:absolute;left:0;top:722px;width:1050px;height:348px;
    background:linear-gradient(180deg,var(--blue) 0%,var(--blue-deep) 55%,#2a5cb8 100%)}
  .plans-title{position:absolute;left:82px;top:742px;font-family:"Bebas Neue",Impact,sans-serif;font-weight:400;font-size:36px;color:var(--white);letter-spacing:.5px}
  .plans-table{position:absolute;left:80px;top:796px;width:444px;border-collapse:separate;border-spacing:3px 10px;
    font-family:"Oswald",Arial,sans-serif;font-size:11.5px;text-align:center}
  .plans-table td,.plans-table th{height:30px;padding:0 3px;font-weight:400}
  .plans-table thead th{background:var(--white);color:var(--grey);text-transform:uppercase}
  .plans-table tbody th{background:var(--grey-dark);color:var(--white);text-transform:uppercase;width:80px;line-height:1.05}
  .plans-table tbody td{background:#e2e4e8;color:var(--grey-dark)}
  .plans-table tbody tr.cost td{background:var(--grey);color:var(--white);font-size:10.5px}
  .footer-rule{position:absolute;left:0;top:1078px;width:1050px;height:6px;background:var(--white)}
  .footer{position:absolute;left:0;top:1088px;width:1050px;height:112px;background:var(--grey);
    display:flex;align-items:center;padding-left:74px;gap:26px;color:var(--white);font-size:24px}
  .contact{display:flex;align-items:center;gap:10px}
  .divider{width:2px;height:46px;background:var(--white)}
  .points{position:absolute;left:548px;top:536px;width:436px;height:664px;background:var(--navy);
    border-radius:26px 26px 0 0;padding:26px 26px 0 28px;color:var(--white)}
  .points h2{font-family:"Bebas Neue",Impact,sans-serif;font-weight:400;font-size:36px;letter-spacing:.5px;margin-bottom:10px}
  .points ul{list-style:none}
  .points li{display:flex;gap:10px;font-size:12.6px;line-height:1.32;margin-bottom:12.5px}
  .points li svg{flex:0 0 14px;margin-top:2px}
</style>
</head>
<body>
<main class="brochure">

  <div class="hero-visual" role="img" aria-label="Large triangle frame with a swoosh, holding a photo of hands with a tablet under a glowing cloud and padlock"></div>

  <div class="brand">
    <span class="brand-mark"></span>
    <span class="brand-name">MERIDANE SYSTEMS</span>
  </div>

  <h1 class="headline">
    <span class="line-navy">Futuristic</span>
    <span class="line-grey">Tech</span>
    <span class="line-navy">Company</span>
  </h1>

  <div class="cloud-strip" role="img" aria-label="Decorative blue and white cloud shapes"></div>

  <p class="intro">Meridane Systems is looking to offer private cloud services for our enterprise customers in Perth-based data-centres that provides our clients with a lower-cost alternative to Kelvara or QNL yielding better performance.</p>

  <div class="plans-band"></div>
  <h2 class="plans-title">Meridane Private Cloud Plans</h2>
  <table class="plans-table">
    <thead>
      <tr><th></th><th>Starter</th><th>Growth</th><th>Professional</th><th>Premier</th><th>Elite</th></tr>
    </thead>
    <tbody>
      <tr><th>Max VMs</th><td>5</td><td>10</td><td>15</td><td>20</td><td>25</td></tr>
      <tr><th>CPU Cores</th><td>8</td><td>16</td><td>32</td><td>43</td><td>64</td></tr>
      <tr><th>Memory (GB)</th><td>64</td><td>128</td><td>192</td><td>256</td><td>320</td></tr>
      <tr><th>Storage<br>SSD (TB)</th><td>3</td><td>8</td><td>15</td><td>20</td><td>30</td></tr>
      <tr class="cost"><th>Monthly Cost</th><td>$ 1,028.01</td><td>$ 3,426.64</td><td>$ 4,626.05</td><td>$ 5,482.72</td><td>$ 7,196.07</td></tr>
    </tbody>
  </table>

  <div class="footer-rule"></div>
  <footer class="footer">
    <span class="contact">
      <svg width="24" height="24" viewBox="0 0 24 24" fill="none" stroke="#fff" stroke-width="1.6" aria-hidden="true"><path d="M5 3h4l2 5-2.5 1.5a11 11 0 0 0 6 6L16 13l5 2v4a2 2 0 0 1-2 2A17 17 0 0 1 3 5a2 2 0 0 1 2-2z"/></svg>
      0400 555 210
    </span>
    <span class="divider"></span>
    <span class="contact">
      <svg width="24" height="24" viewBox="0 0 24 24" fill="none" stroke="#fff" stroke-width="1.6" aria-hidden="true"><circle cx="12" cy="12" r="9.5"/><ellipse cx="12" cy="12" rx="4" ry="9.5"/><path d="M2.5 12h19M4 7h16M4 17h16"/></svg>
      meridanesys.net
    </span>
  </footer>

  <section class="points">
    <h2>Selling Points</h2>
    <ul>
      <li><svg width="14" height="14" viewBox="0 0 14 14" aria-hidden="true"><circle cx="7" cy="7" r="6" fill="none" stroke="#fff"/><path d="M4 7.2l2 2 4-4" fill="none" stroke="#fff" stroke-width="1.2"/></svg>Hosted in a local Perth-based TIER3 and TIER4 datacentres</li>
      <li><svg width="14" height="14" viewBox="0 0 14 14" aria-hidden="true"><circle cx="7" cy="7" r="6" fill="none" stroke="#fff"/><path d="M4 7.2l2 2 4-4" fill="none" stroke="#fff" stroke-width="1.2"/></svg>WA owned hosting - support local</li>
      <li><svg width="14" height="14" viewBox="0 0 14 14" aria-hidden="true"><circle cx="7" cy="7" r="6" fill="none" stroke="#fff"/><path d="M4 7.2l2 2 4-4" fill="none" stroke="#fff" stroke-width="1.2"/></svg>Low latency - ultra fast local hosting</li>
      <li><svg width="14" height="14" viewBox="0 0 14 14" aria-hidden="true"><circle cx="7" cy="7" r="6" fill="none" stroke="#fff"/><path d="M4 7.2l2 2 4-4" fill="none" stroke="#fff" stroke-width="1.2"/></svg>Includes Orvix Host Datacentre licensing</li>
      <li><svg width="14" height="14" viewBox="0 0 14 14" aria-hidden="true"><circle cx="7" cy="7" r="6" fill="none" stroke="#fff"/><path d="M4 7.2l2 2 4-4" fill="none" stroke="#fff" stroke-width="1.2"/></svg>Includes BrakWall Managed Firewalls for Enterprise level threat detection</li>
      <li><svg width="14" height="14" viewBox="0 0 14 14" aria-hidden="true"><circle cx="7" cy="7" r="6" fill="none" stroke="#fff"/><path d="M4 7.2l2 2 4-4" fill="none" stroke="#fff" stroke-width="1.2"/></svg>Includes all infrastructure maintenance services</li>
      <li><svg width="14" height="14" viewBox="0 0 14 14" aria-hidden="true"><circle cx="7" cy="7" r="6" fill="none" stroke="#fff"/><path d="M4 7.2l2 2 4-4" fill="none" stroke="#fff" stroke-width="1.2"/></svg>Full self management of VMs through customer portal</li>
      <li><svg width="14" height="14" viewBox="0 0 14 14" aria-hidden="true"><circle cx="7" cy="7" r="6" fill="none" stroke="#fff"/><path d="M4 7.2l2 2 4-4" fill="none" stroke="#fff" stroke-width="1.2"/></svg>Includes a 1gbps Internet link</li>
      <li><svg width="14" height="14" viewBox="0 0 14 14" aria-hidden="true"><circle cx="7" cy="7" r="6" fill="none" stroke="#fff"/><path d="M4 7.2l2 2 4-4" fill="none" stroke="#fff" stroke-width="1.2"/></svg>Predictable fixed monthly fee with no dynamic billing</li>
      <li><svg width="14" height="14" viewBox="0 0 14 14" aria-hidden="true"><circle cx="7" cy="7" r="6" fill="none" stroke="#fff"/><path d="M4 7.2l2 2 4-4" fill="none" stroke="#fff" stroke-width="1.2"/></svg>No additional charges for Storage Transactions, Internet Usage, VM Snapshots, Datacentre Bandwidth Usage and Firewall Traffic Usage.</li>
      <li><svg width="14" height="14" viewBox="0 0 14 14" aria-hidden="true"><circle cx="7" cy="7" r="6" fill="none" stroke="#fff"/><path d="M4 7.2l2 2 4-4" fill="none" stroke="#fff" stroke-width="1.2"/></svg>Highly available cluster, no single point of failure.</li>
      <li><svg width="14" height="14" viewBox="0 0 14 14" aria-hidden="true"><circle cx="7" cy="7" r="6" fill="none" stroke="#fff"/><path d="M4 7.2l2 2 4-4" fill="none" stroke="#fff" stroke-width="1.2"/></svg>Pricing is based on 36 months commit</li>
      <li><svg width="14" height="14" viewBox="0 0 14 14" aria-hidden="true"><circle cx="7" cy="7" r="6" fill="none" stroke="#fff"/><path d="M4 7.2l2 2 4-4" fill="none" stroke="#fff" stroke-width="1.2"/></svg>Yearly rate increases capped to a maximum of Australian CPI</li>
      <li><svg width="14" height="14" viewBox="0 0 14 14" aria-hidden="true"><circle cx="7" cy="7" r="6" fill="none" stroke="#fff"/><path d="M4 7.2l2 2 4-4" fill="none" stroke="#fff" stroke-width="1.2"/></svg>All plans have 24/7/365 support with dedicated after hours number.</li>
      <li><svg width="14" height="14" viewBox="0 0 14 14" aria-hidden="true"><circle cx="7" cy="7" r="6" fill="none" stroke="#fff"/><path d="M4 7.2l2 2 4-4" fill="none" stroke="#fff" stroke-width="1.2"/></svg>Managed backup and managed disaster recovery services can be added to plans</li>
    </ul>
  </section>

</main>
</body>
</html>
```